We are a recruitment company based in Norwich/Cambridge England.
I have included our company logo which we want to remain the same.

What we are looking for is a new creative Business card which will really stand out!!

Contact Information for Business Card

Harriet Dunmore
email: Harriet@plavex.co.uk
Address: Brackwell House
Fenmoor Enterprise Park
Partridge Way
Norwich
QB9 3KX
Tel:01632 960418

```html
<!DOCTYPE html>
<html lang="en">
<head>
<meta charset="utf-8">
<title>Plavex Business Card</title>
<link rel="stylesheet" href="https://fonts.googleapis.com/css2?family=Work+Sans:wght@400;500;600&display=swap">
<style>
  :root {
    --stage: #2b2b2b;
    --card: #1b1b1b;
    --green: #8cc63f;
    --grey: #8a868c;
    --white: #f4f4f4;
  }
  * { box-sizing: border-box; margin: 0; padding: 0; }
  html, body { width: 1200px; height: 900px; overflow: hidden; }
  body {
    background: var(--stage);
    font-family: "Work Sans", sans-serif;
    color: var(--white);
    position: relative;
  }
  .card {
    position: absolute;
    left: 270px;
    width: 660px;
    height: 377px;
    background: var(--card);
  }
  .card--front { top: 50px; }
  .card--back { top: 473px; overflow: hidden; }

  .brand { display: flex; align-items: center; gap: 14px; }
  .brand__dot { width: 52px; height: 52px; border-radius: 50%; background: var(--green); flex: none; }
  .brand__name { font-weight: 500; font-size: 58px; line-height: 1; letter-spacing: -1px; }
  .brand__tagline { font-size: 11px; letter-spacing: 4px; margin-top: 6px; color: var(--white); }

  .card--front .brand-block { position: absolute; left: 50%; top: 110px; transform: translateX(-50%); }
  .card--front .brand__name { color: var(--white); }
  .card--front .brand__tagline { padding-left: 66px; }
  .front__web { position: absolute; left: 0; right: 0; top: 288px; text-align: center; font-size: 16px; letter-spacing: 1px; }
  .accent { color: var(--green); }

  .card--back .brand-block { position: absolute; left: 40px; top: 42px; }
  .card--back .brand__dot { width: 40px; height: 40px; }
  .card--back .brand__name { font-size: 44px; color: var(--grey); }
  .card--back .brand__tagline { font-size: 9px; letter-spacing: 3px; padding-left: 54px; color: var(--grey); }

  .person { position: absolute; right: 40px; top: 108px; text-align: right; }
  .person__name { color: var(--green); font-size: 27px; font-weight: 500; letter-spacing: 1px; }
  .person__role { font-size: 16px; letter-spacing: 1px; margin-top: 2px; }

  .contacts { position: absolute; left: 40px; top: 208px; list-style: none; font-size: 16px; letter-spacing: .5px; }
  .contacts li { display: flex; align-items: center; gap: 12px; height: 24px; }
  .contacts svg { width: 12px; height: 12px; flex: none; }
  .address { position: absolute; left: 40px; top: 300px; font-size: 15px; font-style: normal; line-height: 24px; letter-spacing: .5px; }

  .mark-area {
    position: absolute;
    left: 400px; top: 190px;
    width: 270px; height: 270px;
    border-radius: 50%;
    background: var(--green);
  }
</style>
</head>
<body>
  <section class="card card--front">
    <div class="brand-block">
      <div class="brand">
        <span class="brand__dot"></span>
        <span class="brand__name">Plavex</span>
      </div>
      <p class="brand__tagline">Technology Recruitment</p>
    </div>
    <p class="front__web">www.<span class="accent">plavex</span>.co.uk</p>
  </section>

  <section class="card card--back">
    <div class="brand-block">
      <div class="brand">
        <span class="brand__dot"></span>
        <span class="brand__name">Plavex</span>
      </div>
      <p class="brand__tagline">Technology Recruitment</p>
    </div>

    <div class="person">
      <p class="person__name">Harriet Dunmore</p>
      <p class="person__role">Founder</p>
    </div>

    <ul class="contacts">
      <li>
        <svg viewBox="0 0 12 12" aria-hidden="true"><path d="M3 1l2 2.5-1.2 1.2a6 6 0 0 0 3.5 3.5L8.5 7 11 9l-1.5 2C5 11 1 7 1 2.5z" fill="var(--green)"/></svg>
        01632 960418
      </li>
      <li>
        <svg viewBox="0 0 12 12" aria-hidden="true"><rect x="1" y="2.5" width="10" height="7" fill="none" stroke="var(--green)" stroke-width="1.2"/><path d="M1 2.5l5 4 5-4" fill="none" stroke="var(--green)" stroke-width="1.2"/></svg>
        Harriet@plavex.co.uk
      </li>
      <li>
        <svg viewBox="0 0 12 12" aria-hidden="true"><circle cx="6" cy="6" r="5" fill="none" stroke="var(--green)" stroke-width="1.2"/><path d="M1 6h10M6 1c-2.5 3-2.5 7 0 10M6 1c2.5 3 2.5 7 0 10" fill="none" stroke="var(--green)" stroke-width="1"/></svg>
        <span>www.<span class="accent">plavex</span>.co.uk</span>
      </li>
    </ul>

    <address class="address">
      Brackwell House, Fenmoor Enterprise Park<br>
      Partridge Way, Norwich QB9 3KX
    </address>

    <div class="mark-area" role="img" aria-label="Large brand mark decoration"></div>
  </section>
</body>
</html>
```